Shopify Web-Page "Tiny-ThreadDays

We are building a new business in Switzerland offering premium sewing holiday camps for kids aged 9–14. In enclosed brief outlines our requirements for a complete Shopify homepage design and a multilingual logo creation.
Domains: tiny-threaddays.ch ; tiny-giornifilo.ch ; tiny-fadentage.ch

Project Overview
We are looking for:
1. A modern, fully designed Shopify homepage in English using standard Shopify content blocks (no custom coding), which we can later update ourselves. Supporting Multilanguage (EN, German, Italian).

2. A logo design that includes the brand identity and communicates our multilingual, creative, and child-focused positioning.

All details in enclosed

```html
<!DOCTYPE html>
<html lang="en">
<head>
<meta charset="utf-8">
<title>Tiny-ThreadDays – Creative Sewing Holidays for Kids</title>
<link href="https://fonts.googleapis.com/css2?family=Roboto+Condensed:wght@400;700&family=Inter:wght@400;500;600&display=swap" rel="stylesheet">
<style>
:root{
  --pink:#d9687a;
  --teal:#3ea5ab;
  --ink:#1e2633;
  --text:#4a4f58;
  --muted:#6b7079;
  --cream:#f3efe9;
  --blush:#f9f1f0;
  --line:#e6e1de;
  --footer:#2a2a2b;
  --white:#ffffff;
}
*{box-sizing:border-box;margin:0;padding:0}
html,body{width:1200px;height:4658px;overflow:hidden}
body{font-family:"Inter",Arial,sans-serif;color:var(--text);background:var(--white);position:relative}
.heading{font-family:"Roboto Condensed","Arial Narrow",sans-serif;font-weight:700;color:var(--ink);text-transform:uppercase;letter-spacing:.2px}
.heading span{color:var(--pink)}
.rule{width:85px;height:3px;background:var(--pink);border-radius:2px}
.center{text-align:center}
section,header,footer{position:absolute;left:0;width:1200px}

/* header */
.site-header{top:0;height:78px;background:var(--cream)}
.brand{position:absolute;left:145px;top:24px;display:flex;align-items:center;gap:8px;font-size:17px;font-weight:600;color:var(--teal)}
.brand i{width:22px;height:22px;border-radius:50%;background:var(--pink);display:block}
.nav{position:absolute;left:500px;top:31px;display:flex;gap:25px;font-size:12.5px;color:#3b3f47}
.nav a{color:inherit;text-decoration:none}
.nav .active{font-weight:600;color:var(--ink)}
.lang{position:absolute;left:940px;top:20px;width:117px;height:37px;border:1px solid #5a5f67;border-radius:4px;display:flex;align-items:center;gap:7px;padding:0 10px;font-size:12.5px;color:#3b3f47}
.lang .caret{margin-left:auto}

/* hero */
.hero{top:78px;height:564px;background:linear-gradient(90deg,#2c2c2e 0%,#3d3a39 38%,#8b7a6c 70%,#b8a48f 100%);overflow:hidden}
.hero-photo{position:absolute;right:0;top:0;width:640px;height:564px;background:radial-gradient(ellipse at 60% 50%,#c9b49c 0%,#8e7966 55%,rgba(70,62,58,0) 100%)}
.hero-copy{position:absolute;left:143px;top:70px;color:var(--white)}
.hero-copy .t1{font-family:"Roboto Condensed",sans-serif;font-size:41px;font-weight:400;line-height:48px}
.hero-copy .t2{font-family:"Roboto Condensed",sans-serif;font-size:47px;font-weight:700;line-height:56px}
.hero-copy .rule{background:var(--white);margin:22px 0 28px}
.hero-copy p{font-size:15px;line-height:28px;width:400px}
.ticks{margin-top:44px;list-style:none;font-size:13px}
.ticks li{display:flex;align-items:center;gap:12px;margin-bottom:19px}
.btn{display:inline-flex;align-items:center;justify-content:center;border-radius:22px;font-size:13px;font-weight:600;text-decoration:none}
.btn-teal{background:var(--teal);color:var(--white)}
.hero .btn{position:absolute;left:143px;top:444px;width:210px;height:41px}
.scroll-cue{position:absolute;left:570px;top:612px;width:60px;height:60px;border-radius:50%;background:var(--white);box-shadow:0 6px 18px rgba(0,0,0,.12);display:flex;align-items:center;justify-content:center;z-index:2}

/* about */
.about{top:642px;height:574px}
.about-img-back{position:absolute;left:143px;top:81px;width:336px;height:322px;background:linear-gradient(135deg,#e8e2dc,#c9a58e 55%,#efe9e3)}
.about-img-front{position:absolute;left:270px;top:248px;width:298px;height:251px;border:6px solid var(--white);background:linear-gradient(135deg,#b59a83,#d8c4b1 50%,#8f7a69)}
.about-copy{position:absolute;left:598px;top:95px;width:460px}
.about-copy .heading{font-size:31px}
.about-copy .rule{margin:12px 0 26px}
.about-copy p{font-size:12px;line-height:22px;margin-bottom:12px}
.about-copy .btn{width:177px;height:42px;margin-top:16px}

/* how it works */
.how{top:1216px;height:464px;background:var(--blush)}
.how .heading{position:absolute;top:85px;width:100%;font-size:31px}
.sub{font-size:12px;line-height:22px;color:var(--text)}
.how .sub{position:absolute;top:166px;left:290px;width:620px}
.steps{position:absolute;top:226px;left:0;width:1200px}
.step{position:absolute;width:180px;text-align:center;transform:translateX(-50%)}
.step svg{display:block;margin:0 auto 8px}
.step h3{font-size:13.5px;font-weight:500;color:var(--ink);margin-bottom:6px}
.step p{font-size:11.5px;line-height:19px;color:var(--muted)}
.arrow{position:absolute;top:18px;width:112px;height:8px}

/* why */
.why{top:1680px;height:651px}
.why .heading{position:absolute;top:78px;width:100%;font-size:31px}
.why .sub{position:absolute;top:158px;left:320px;width:560px}
.card{position:absolute;width:283px;height:168px;border:1px solid var(--line);border-radius:4px;background:var(--white);text-align:center;box-shadow:0 2px 8px rgba(0,0,0,.03)}
.card.featured{border-color:var(--pink)}
.card .ico{width:54px;height:54px;border-radius:50%;background:#eef6f6;margin:26px auto 0;display:flex;align-items:center;justify-content:center}
.card.featured .ico{background:var(--pink)}
.card p{font-size:13px;line-height:24px;color:var(--ink);margin-top:16px;padding:0 22px}

/* camps */
.camps{top:2331px;height:650px}
.camps .heading{position:absolute;top:40px;width:100%;font-size:31px}
.camps .sub{position:absolute;top:106px;width:100%}
.camp{position:absolute;top:152px;width:283px;height:418px;border:1px solid var(--line);border-radius:4px;overflow:hidden;background:var(--white)}
.camp-img{height:161px}
.camp-body{padding:16px 14px}
.camp h3{font-size:13.5px;font-weight:600;color:var(--ink);margin-bottom:8px}
.camp .desc{font-size:11.5px;line-height:20px;color:var(--muted);height:84px}
.meta{display:grid;grid-template-columns:1fr 1fr;row-gap:14px;font-size:11.5px;color:var(--muted);margin-top:8px}
.meta b{color:var(--ink);font-weight:600;margin-right:12px}
.book{display:inline-flex;align-items:center;gap:6px;margin-top:22px;font-size:12.5px;color:var(--teal);text-decoration:underline}

/* faq */
.faq{top:2981px;height:1117px;background:#f8f8f8}
.faq .heading{position:absolute;top:80px;width:100%;font-size:31px}
.faq .rule{position:absolute;top:130px;left:557px}
.faq .sub{position:absolute;top:148px;width:100%}
.faq-item{position:absolute;left:175px;width:848px;height:65px;background:var(--white);border-left:4px solid var(--pink);box-shadow:0 2px 10px rgba(0,0,0,.05);padding:0 22px;display:flex;align-items:center;font-size:14px;font-weight:500;color:var(--ink)}
.faq-item svg{margin-left:auto}
.faq-item.open{height:112px;align-items:flex-start;flex-direction:column;justify-content:center}
.faq-item.open .q{display:flex;width:100%;align-items:center}
.faq-item.open p{font-size:11.5px;line-height:20px;color:var(--muted);font-weight:400;margin-top:8px;width:720px}

/* cta */
.cta{top:4098px;height:212px;background:linear-gradient(90deg,#3fa3a9,#55b4b8 60%,#4aa8ad)}
.cta h2{position:absolute;left:141px;top:62px;font-family:"Roboto Condensed",sans-serif;font-size:28px;color:var(--white);text-transform:uppercase}
.cta p{position:absolute;left:141px;top:112px;width:600px;font-size:14px;line-height:26px;color:#f1fbfb}
.cta .btn{position:absolute;left:882px;top:85px;width:175px;height:42px;background:var(--white);color:var(--teal);font-size:14px}

/* footer */
.site-footer{top:4310px;height:348px;background:var(--footer);color:#d9d9d9}
.foot-brand{position:absolute;left:145px;top:85px;font-size:22px;font-weight:600;color:var(--teal);display:flex;align-items:center;gap:10px}
.foot-brand i{width:26px;height:26px;border-radius:50%;background:var(--pink);display:block}
.follow{position:absolute;left:144px;top:223px;display:flex;align-items:center;gap:8px;font-size:12px}
.follow span{width:20px;height:20px;border-radius:50%;border:1px solid #8a8a8a;display:block}
.follow span.on{background:var(--pink);border-color:var(--pink)}
.fcol{position:absolute;top:73px}
.fcol h4{font-size:14px;font-weight:500;color:#e8b13c;margin-bottom:18px}
.fcol ul{list-style:none;font-size:12.5px;line-height:29px}
.contact li{display:flex;align-items:center;gap:16px;line-height:20px;margin-bottom:16px}
.contact .ci{width:30px;height:30px;border-radius:50%;background:#444;display:flex;align-items:center;justify-content:center;flex:none}
.contact .ci.pink{background:var(--pink)}
.news p{font-size:12.5px;line-height:22px;width:230px}
.news .field{margin-top:14px;width:246px;height:31px;border-radius:16px;background:var(--white);display:flex;align-items:center;padding:0 4px 0 12px;gap:6px;font-size:11px;color:#999}
.news .go{margin-left:auto;width:24px;height:24px;border-radius:50%;background:var(--pink);display:flex;align-items:center;justify-content:center}
.copyright{position:absolute;left:0;top:289px;width:100%;border-top:1px solid #444;padding-top:22px;text-align:center;font-size:11px;color:#bdbdbd}
</style>
</head>
<body>

<header class="site-header">
  <div class="brand"><i></i>Tiny-ThreadDays</div>
  <nav class="nav">
    <a class="active" href="#">Home</a><a href="#">About Us</a><a href="#">Camps</a><a href="#">How It Works</a><a href="#">FAQs</a><a href="#">Contact</a>
  </nav>
  <div class="lang">
    <svg width="15" height="15" viewBox="0 0 24 24" fill="none" stroke="#3b3f47" stroke-width="1.8"><circle cx="12" cy="12" r="9"/><path d="M3 12h18M12 3c3 3 3 15 0 18M12 3c-3 3-3 15 0 18"/></svg>
    English
    <svg class="caret" width="12" height="12" viewBox="0 0 24 24" fill="none" stroke="#3b3f47" stroke-width="2.5"><path d="M6 9l6 6 6-6"/></svg>
  </div>
</header>

<section class="hero">
  <div class="hero-photo" role="img" aria-label="Sewing instructor helping a boy at a sewing machine in a bright studio"></div>
  <div class="hero-copy">
    <div class="t1">CREATIVE SEWING</div>
    <div class="t2">HOLIDAYS FOR KIDS</div>
    <div class="rule"></div>
    <p>Creative fun in Zurich – Multilingual and Inspiring! Learn sewing, build confidence, and create unique fashion pieces in our small-group camps.</p>
    <ul class="ticks">
      <li><svg width="17" height="17" viewBox="0 0 24 24"><circle cx="12" cy="12" r="11" fill="#c9b3d8"/><path d="M7 12l3.5 3.5L17 9" fill="none" stroke="#3a2d4a" stroke-width="2.4"/></svg>Crafting Fun, One Stitch at a Time</li>
      <li><svg width="17" height="17" viewBox="0 0 24 24"><circle cx="12" cy="12" r="11" fill="#c9b3d8"/><path d="M7 12l3.5 3.5L17 9" fill="none" stroke="#3a2d4a" stroke-width="2.4"/></svg>Multilingual Creativity, Made Just for Kids</li>
    </ul>
  </div>
  <a class="btn btn-teal" href="#">View Upcoming Camps</a>
</section>
<div class="scroll-cue">
  <svg width="22" height="30" viewBox="0 0 22 30" fill="none" stroke="#2a2a2a" stroke-width="1.8"><rect x="2" y="2" width="18" height="26" rx="9"/><path d="M11 8v6M8 12l3 3 3-3"/></svg>
</div>

<section class="about">
  <div class="about-img-back" role="img" aria-label="Girl smiling while threading a needle"></div>
  <div class="about-img-front" role="img" aria-label="Mother and daughter sewing together at a machine"></div>
  <div class="about-copy">
    <h2 class="heading">About Our <span>Camps</span></h2>
    <div class="rule"></div>
    <p>At Tiny-ThreadDays, we believe in nurturing creativity while having fun. Our experienced instructors create a safe, inspiring environment where children can explore their creative potential.</p>
    <p>With over 10 years of experience in teaching children sewing, tailoring, and design, Lena and Marta guide young talents through a creative week of vacation – with real results: self-sewn pieces, new friends, and lots of pride.</p>
    <p>At the last day, the children show off their success, their own sewn unique pieces, in a sympathetic fashion show. Join our premium sewing camps in Zurich where children aged 9-14 discover creativity, build confidence, and make new friends while learning to sew in a fun, supportive environment</p>
    <a class="btn btn-teal" href="#">Book camp Now</a>
  </div>
</section>

<section class="how">
  <h2 class="heading center">How Our Camps <span>Work</span></h2>
  <p class="sub center">Lena and Marta bring over 10 years of experience teaching children sewing, tailoring, and design with fun, style, and structure.</p>
  <div class="steps">
    <div class="step" style="left:166px">
      <svg width="44" height="38" viewBox="0 0 44 38" fill="none" stroke="#d9687a" stroke-width="1.6"><path d="M8 34L30 8M26 6l8 8M30 8c3-4 8-4 10 0"/><circle cx="14" cy="26" r="4"/></svg>
      <h3>Project Selection</h3>
      <p>Your child chooses their own model based on previously produced clothing items and sewing patterns.</p>
    </div>
    <svg class="arrow" style="left:218px" viewBox="0 0 112 8"><path d="M0 4h106" stroke="#d9687a" stroke-dasharray="3 3"/><path d="M106 1l4 3-4 3" fill="none" stroke="#d9687a"/></svg>
    <div class="step" style="left:383px">
      <svg width="44" height="38" viewBox="0 0 44 38" fill="none" stroke="#d9687a" stroke-width="1.6"><path d="M10 6h24v26H10zM10 14h24M10 22h24M18 6v26M26 6v26"/></svg>
      <h3>Fabric selection</h3>
      <p>High-quality fabrics are available.</p>
    </div>
    <svg class="arrow" style="left:435px" viewBox="0 0 112 8"><path d="M0 4h106" stroke="#d9687a" stroke-dasharray="3 3"/><path d="M106 1l4 3-4 3" fill="none" stroke="#d9687a"/></svg>
    <div class="step" style="left:600px">
      <svg width="44" height="38" viewBox="0 0 44 38" fill="none" stroke="#d9687a" stroke-width="1.6"><path d="M6 32h32M8 32V12h26v8H16v12M34 12v16M30 28h8"/><circle cx="26" cy="16" r="1.5"/></svg>
      <h3>Sewing machine</h3>
      <p>Learn how to use a sewing machine</p>
    </div>
    <svg class="arrow" style="left:652px" viewBox="0 0 112 8"><path d="M0 4h106" stroke="#d9687a" stroke-dasharray="3 3"/><path d="M106 1l4 3-4 3" fill="none" stroke="#d9687a"/></svg>
    <div class="step" style="left:817px">
      <svg width="44" height="38" viewBox="0 0 44 38" fill="none" stroke="#d9687a" stroke-width="1.6"><path d="M12 4h20l-4 14h-12zM22 18v16M16 34h12M14 10h16"/></svg>
      <h3>Sewing &amp; refining</h3>
      <p>Step by step to the goal with professional guidance</p>
    </div>
    <svg class="arrow" style="left:869px" viewBox="0 0 112 8"><path d="M0 4h106" stroke="#d9687a" stroke-dasharray="3 3"/><path d="M106 1l4 3-4 3" fill="none" stroke="#d9687a"/></svg>
    <div class="step" style="left:1032px">
      <svg width="44" height="38" viewBox="0 0 44 38" fill="none" stroke="#d9687a" stroke-width="1.6"><path d="M14 4l-6 6 4 4v20h20V14l4-4-6-6-4 4h-8z"/><path d="M18 20l8 6"/></svg>
      <h3>Showtime!</h3>
      <p>Fashion show or photo shoot at the end of the week</p>
    </div>
  </div>
</section>

<section class="why">
  <h2 class="heading center">Why Parents <span>Choose Us</span></h2>
  <p class="sub center">Why Families Love Tiny-ThreadDays Sewing Camps. Small groups of maximum 8 children for personalized attention</p>

  <div class="card" style="left:141px;top:221px">
    <div class="ico"><svg width="22" height="22" viewBox="0 0 24 24" fill="none" stroke="#3ea5ab" stroke-width="2"><path d="M4 4l7 7M11 5v6H5M20 20l-7-7M13 19v-6h6"/></svg></div>
    <p>Small groups &amp;<br>personalized attention</p>
  </div>
  <div class="card featured" style="left:459px;top:221px">
    <div class="ico"><svg width="24" height="24" viewBox="0 0 24 24" fill="none" stroke="#fff" stroke-width="1.8"><path d="M3 5h10M8 3v2M5 5c1 4 4 7 8 8M11 5c-1 4-4 7-8 9M13 21l4-10 4 10M14.5 17h5"/></svg></div>
    <p>Multilingual supervision<br>(DE / EN / IT)</p>
  </div>
  <div class="card" style="left:775px;top:221px">
    <div class="ico"><svg width="22" height="22" viewBox="0 0 24 24" fill="#3ea5ab"><path d="M12 2a7 7 0 00-7 7c0 5 7 13 7 13s7-8 7-13a7 7 0 00-7-7z"/><circle cx="12" cy="9" r="2.6" fill="#eef6f6"/></svg></div>
    <p>Pick-up Service from the<br>Main-Station</p>
  </div>
  <div class="card" style="left:141px;top:425px">
    <div class="ico"><svg width="24" height="24" viewBox="0 0 24 24" fill="none" stroke="#3ea5ab" stroke-width="1.6"><path d="M12 3l2.7 5.6 6.1.9-4.4 4.3 1 6.1L12 17l-5.4 2.9 1-6.1L3.2 9.5l6.1-.9z"/></svg></div>
    <p>Encouragement of creativity, self-confidence, and fine motor skills</p>
  </div>
  <div class="card" style="left:459px;top:425px">
    <div class="ico"><svg width="22" height="22" viewBox="0 0 24 24" fill="none" stroke="#3ea5ab" stroke-width="1.6"><path d="M12 3l8 3v6c0 5-4 8-8 9-4-1-8-4-8-9V6z"/><path d="M8.5 12l2.5 2.5 4.5-5"/></svg></div>
    <p>Safe, loving environment in Zurich, various places easy to reach</p>
  </div>
  <div class="card" style="left:775px;top:425px">
    <div class="ico"><svg width="24" height="24" viewBox="0 0 24 24" fill="none" stroke="#3ea5ab" stroke-width="1.4"><path d="M4 4h16v16H4zM4 8h16M4 12h16M4 16h16M8 4v16M12 4v16M16 4v16"/></svg></div>
    <p>High-quality fabrics &amp; top-quality sewing machines (Stitchwell)</p>
  </div>
</section>

<section class="camps">
  <h2 class="heading center">Our Upcoming <span>Camps</span></h2>
  <p class="sub center">Real results: self-sewn pieces, new friends, and lots of pride. Culminating fashion show to celebrate achievements</p>

  <article class="camp" style="left:141px">
    <div class="camp-img" role="img" aria-label="Children sewing colourful fabric at a table with a teacher" style="background:linear-gradient(135deg,#c7a58d,#e6d6c6 55%,#9a8677)"></div>
    <div class="camp-body">
      <h3>Spring Sewing Camp</h3>
      <p class="desc">Join us for a creative week during spring break! Children will learn sewing basics and create their own spring-themed projects.</p>
      <div class="meta"><div><b>Age:</b>09 to 14</div><div><b>Total:</b>200 Kids</div><div><b>Date:</b>21 Oct,2025</div><div><b>Duration:</b>06 Days</div></div>
      <a class="book" href="#">Book Now <svg width="14" height="8" viewBox="0 0 14 8" fill="none" stroke="#3ea5ab" stroke-width="1.4"><path d="M0 4h12M9 1l3 3-3 3"/></svg></a>
    </div>
  </article>
  <article class="camp" style="left:459px">
    <div class="camp-img" role="img" aria-label="Group of children running across a sunny park" style="background:linear-gradient(180deg,#6f8f4e,#9bbd62 55%,#7a9b48)"></div>
    <div class="camp-body">
      <h3>Summer Fashion Camp</h3>
      <p class="desc">Our popular summer program where kids design and create their own summer wardrobe items in a fun, supportive environment.</p>
      <div class="meta"><div><b>Age:</b>09 to 14</div><div><b>Total:</b>200 Kids</div><div><b>Date:</b>07 Jul,2025</div><div><b>Duration:</b>06 Days</div></div>
      <a class="book" href="#">Book Now <svg width="14" height="8" viewBox="0 0 14 8" fill="none" stroke="#3ea5ab" stroke-width="1.4"><path d="M0 4h12M9 1l3 3-3 3"/></svg></a>
    </div>
  </article>
  <article class="camp" style="left:775px">
    <div class="camp-img" role="img" aria-label="Teacher and children working on garments in a studio" style="background:linear-gradient(135deg,#a89584,#d9c9b8 55%,#8d7b6d)"></div>
    <div class="camp-body">
      <h3>Autumn Creative Camp</h3>
      <p class="desc">Get ready for cooler weather by creating cozy autumn accessories and clothing items in this creative camp Autumn Creative Camp.</p>
      <div class="meta"><div><b>Age:</b>09 to 14</div><div><b>Total:</b>200 Kids</div><div><b>Date:</b>21 Oct,2025</div><div><b>Duration:</b>06 Days</div></div>
      <a class="book" href="#">Book Now <svg width="14" height="8" viewBox="0 0 14 8" fill="none" stroke="#3ea5ab" stroke-width="1.4"><path d="M0 4h12M9 1l3 3-3 3"/></svg></a>
    </div>
  </article>
</section>

<section class="faq">
  <h2 class="heading center">Frequently Asked Questions</h2>
  <div class="rule"></div>
  <p class="sub center">Real results: self-sewn pieces, new friends, and lots of pride. Culminating fashion show to celebrate achievements</p>

  <div class="faq-item open" style="top:196px">
    <div class="q">Does my child need any prior knowledge?<svg width="14" height="14" viewBox="0 0 24 24" fill="none" stroke="#6b7079" stroke-width="2.4"><path d="M6 15l6-6 6 6"/></svg></div>
    <p>We welcome children aged 9-14 years. This age range ensures that participants have the fine motor skills needed for sewing while still being excited about creative projects.</p>
  </div>
  <div class="faq-item" style="top:328px">How does the pick-up service work?<svg width="14" height="14" viewBox="0 0 24 24" fill="none" stroke="#6b7079" stroke-width="2.4"><path d="M6 9l6 6 6-6"/></svg></div>
  <div class="faq-item" style="top:409px">How many items of clothing are produced?<svg width="14" height="14" viewBox="0 0 24 24" fill="none" stroke="#6b7079" stroke-width="2.4"><path d="M6 9l6 6 6-6"/></svg></div>
  <div class="faq-item" style="top:490px">What should my child bring to camp?<svg width="14" height="14" viewBox="0 0 24 24" fill="none" stroke="#6b7079" stroke-width="2.4"><path d="M6 9l6 6 6-6"/></svg></div>
  <div class="faq-item" style="top:571px">What are the camp hours?<svg width="14" height="14" viewBox="0 0 24 24" fill="none" stroke="#6b7079" stroke-width="2.4"><path d="M6 9l6 6 6-6"/></svg></div>
  <div class="faq-item" style="top:652px">We offer pick-up from Zurich Main Station at times. Parents can arrange this during booking<svg width="14" height="14" viewBox="0 0 24 24" fill="none" stroke="#6b7079" stroke-width="2.4"><path d="M6 9l6 6 6-6"/></svg></div>
  <div class="faq-item" style="top:733px">What is your cancellation policy?<svg width="14" height="14" viewBox="0 0 24 24" fill="none" stroke="#6b7079" stroke-width="2.4"><path d="M6 9l6 6 6-6"/></svg></div>
  <div class="faq-item" style="top:814px">How many items of clothing are produced?<svg width="14" height="14" viewBox="0 0 24 24" fill="none" stroke="#6b7079" stroke-width="2.4"><path d="M6 9l6 6 6-6"/></svg></div>
  <div class="faq-item" style="top:895px">Each child completes their own unique clothing item during the week<svg width="14" height="14" viewBox="0 0 24 24" fill="none" stroke="#6b7079" stroke-width="2.4"><path d="M6 9l6 6 6-6"/></svg></div>
  <div class="faq-item" style="top:976px">What safety measures are in place?<svg width="14" height="14" viewBox="0 0 24 24" fill="none" stroke="#6b7079" stroke-width="2.4"><path d="M6 9l6 6 6-6"/></svg></div>
</section>

<section class="cta">
  <h2>Ready for a Creative Adventure?</h2>
  <p>Spaces are limited to 8 children per camp to ensure personalized attention. Book now to secure your child's spot!</p>
  <a class="btn" href="#">View All Camps</a>
</section>

<footer class="site-footer">
  <div class="foot-brand"><i></i>Tiny-ThreadDays</div>
  <div class="follow">Follow Us: <span></span><span class="on"></span><span></span></div>

  <div class="fcol" style="left:364px">
    <h4>Quick Links</h4>
    <ul><li>Home</li><li>About Us</li><li>Camps</li><li>How It Works</li><li>Contact</li></ul>
  </div>

  <div class="fcol contact" style="left:515px">
    <h4>Contact Us</h4>
    <ul>
      <li><span class="ci"><svg width="14" height="14" viewBox="0 0 24 24" fill="none" stroke="#ddd" stroke-width="2"><path d="M12 2a7 7 0 00-7 7c0 5 7 13 7 13s7-8 7-13a7 7 0 00-7-7z"/><circle cx="12" cy="9" r="2.5"/></svg></span>B-45, Fadenweg Studio Lane<br>Zurich, Switzerland</li>
      <li><span class="ci pink"><svg width="14" height="14" viewBox="0 0 24 24" fill="#fff"><path d="M6.6 10.8a15 15 0 006.6 6.6l2.2-2.2a1 1 0 011-.25 11.4 11.4 0 003.6.57 1 1 0 011 1V20a1 1 0 01-1 1A17 17 0 013 4a1 1 0 011-1h3.5a1 1 0 011 1 11.4 11.4 0 00.57 3.6 1 1 0 01-.25 1z"/></svg></span>Phone: (041)-555 0192</li>
      <li><span class="ci"><svg width="14" height="14" viewBox="0 0 24 24" fill="#ddd"><path d="M3 5h18v14H3z"/><path d="M3 5l9 8 9-8" fill="none" stroke="#444" stroke-width="2"/></svg></span>info@tiny-threaddays.ch</li>
    </ul>
  </div>

  <div class="fcol news" style="left:811px">
    <h4>Subscribe to newsletter</h4>
    <p>latest updates, exclusive content, and special offers? Subscribe to our newsletter!</p>
    <div class="field">
      <svg width="12" height="12" viewBox="0 0 24 24" fill="none" stroke="#aaa" stroke-width="2"><path d="M3 5h18v14H3zM3 5l9 8 9-8"/></svg>
      Your Email
      <span class="go"><svg width="12" height="12" viewBox="0 0 24 24" fill="none" stroke="#fff" stroke-width="2.6"><path d="M5 12h13M13 6l6 6-6 6"/></svg></span>
    </div>
  </div>

  <div class="copyright">© 2025 Tiny-ThreadDays. All Rights Reserved.</div>
</footer>

</body>
</html>
```